Business Card Design For Office Furniture Clearance Company

Kestrel Office Clearance - our company name pretty much explains what we do, we clear offices for high end clients, mainly plc's and large international companies.

We require a nice looking business card that displays professionalism but without being too serious.

It would be nice to see just a little more than a conventional boring business card, make sure you add some flare.

Industry/Entity Type

Office Furniture

Contact Information for Business Card

CARD 1

Mark Holloway
Director
mark@kestrelofficeclearance.co.uk
m: 07700 153928

t: 01632 960418
www.kestrelofficeclearance.co.uk

Kestrel Office Clearance
Unit K4 B
2-8 Fenwick Lane
Bletchley
Milton Keynes
ZZ9 4QT

free office clearances… you cant get better than that.

CARD 2

Peter Radford
Director
peter@kestrelofficeclearance.co.uk
m: 07700 382615

t: 01632 960418

Kestrel Office Clearance
Unit K4 B
2-8 Fenwick Lane
Bletchley
Milton Keynes
ZZ9 4QT

Font styles to use
Sans Serif

Requirements
Must have
• A white background - as we have a blue logo.
Nice to have
• Nice use of the logo - play around with this and dissect it.

```html
<!DOCTYPE html>
<html lang="en">
<head>
<meta charset="utf-8">
<title>Kestrel Office Clearance – Business Card</title>
<link href="https://fonts.googleapis.com/css2?family=Lato:wght@400;700&display=swap" rel="stylesheet">
<style>
  :root {
    --page-bg: #e9e7e4;
    --card-bg: #ffffff;
    --brand-blue: #1f5f95;
    --band-blue: #0f5c99;
    --disc-blue: #0a4777;
    --ring-light: rgba(255,255,255,0.85);
    --text-dark: #3b3b3b;
    --text-light: #ffffff;
  }
  html, body {
    margin: 0;
    padding: 0;
    width: 1200px;
    height: 970px;
    overflow: hidden;
    background: var(--page-bg);
    font-family: "Lato", sans-serif;
  }
  .business-card {
    position: absolute;
    left: 100px;
    top: 207px;
    width: 1000px;
    height: 556px;
    border-radius: 22px;
    background: var(--card-bg);
    overflow: hidden;
    box-shadow: 0 14px 40px rgba(0,0,0,0.14);
  }
  .brand-band {
    position: absolute;
    left: 731px;
    top: 0;
    width: 269px;
    height: 100%;
    background: var(--band-blue);
  }
  .brand-disc {
    position: absolute;
    left: 477px;
    top: 17px;
    width: 522px;
    height: 522px;
    border-radius: 50%;
    background: var(--disc-blue);
    display: flex;
    align-items: center;
    justify-content: center;
  }
  .brand-ring {
    position: absolute;
    left: 500px;
    top: 32px;
    width: 496px;
    height: 496px;
    border-radius: 50%;
    border: 2px solid var(--ring-light);
    clip-path: inset(0 0 0 45%);
  }
  .brand-disc-name {
    color: var(--text-light);
    font-weight: 700;
    font-size: 40px;
    line-height: 1.15;
    text-align: center;
  }
  .company-name {
    position: absolute;
    left: 45px;
    top: 48px;
    margin: 0;
    font-size: 43px;
    font-weight: 700;
    color: var(--brand-blue);
    letter-spacing: -0.3px;
  }
  .person {
    position: absolute;
    left: 45px;
    top: 195px;
  }
  .person-name {
    margin: 0;
    font-size: 34px;
    font-weight: 700;
    color: var(--brand-blue);
    line-height: 1.1;
  }
  .person-role {
    margin: 2px 0 0;
    font-size: 22px;
    color: var(--text-dark);
  }
  .address {
    position: absolute;
    left: 45px;
    top: 300px;
    margin: 0;
    font-style: normal;
    font-size: 22px;
    line-height: 28px;
    color: var(--text-dark);
  }
  .contact-list {
    position: absolute;
    left: 45px;
    top: 404px;
    margin: 0;
    padding: 0;
    list-style: none;
    font-size: 22px;
    color: var(--text-dark);
  }
  .contact-item {
    display: flex;
    align-items: center;
    height: 30px;
  }
  .contact-icon {
    width: 22px;
    height: 22px;
    margin-right: 12px;
    flex: none;
    fill: none;
    stroke: var(--disc-blue);
    stroke-width: 2;
  }
  .contact-icon.solid {
    fill: var(--disc-blue);
    stroke: none;
  }
</style>
</head>
<body>
  <section class="business-card">
    <div class="brand-band"></div>
    <div class="brand-disc">
      <span class="brand-disc-name">Kestrel<br>Office<br>Clearance</span>
    </div>
    <div class="brand-ring"></div>

    <h1 class="company-name">Kestrel Office Clearance</h1>

    <div class="person">
      <p class="person-name">Mark Holloway</p>
      <p class="person-role">Director</p>
    </div>

    <address class="address">
      Unit K4 B, 2-8 Fenwick Lane<br>
      Ashbury, Northfield Vale<br>
      ZZ9 4QT
    </address>

    <ul class="contact-list">
      <li class="contact-item">
        <svg class="contact-icon" viewBox="0 0 24 24"><rect x="6" y="2" width="12" height="20" rx="2"/><line x1="10" y1="18" x2="14" y2="18"/></svg>
        07700 153928
      </li>
      <li class="contact-item">
        <svg class="contact-icon solid" viewBox="0 0 24 24"><path d="M6.6 10.8c1.4 2.8 3.8 5.1 6.6 6.6l2.2-2.2c.3-.3.7-.4 1-.2 1.1.4 2.3.6 3.6.6.6 0 1 .4 1 1V20c0 .6-.4 1-1 1C10.6 21 3 13.4 3 4c0-.6.4-1 1-1h3.5c.6 0 1 .4 1 1 0 1.3.2 2.5.6 3.6.1.3 0 .7-.2 1z"/></svg>
        01632 960418
      </li>
      <li class="contact-item">
        <svg class="contact-icon solid" viewBox="0 0 24 24"><path d="M2 5h20v14H2z"/><path d="M2 5l10 8 10-8" fill="none" stroke="#fff" stroke-width="1.8"/></svg>
        mark@kestrelofficeclearance.co.uk
      </li>
      <li class="contact-item">
        <svg class="contact-icon" viewBox="0 0 24 24"><circle cx="12" cy="12" r="9.5"/><ellipse cx="12" cy="12" rx="4" ry="9.5"/><line x1="2.5" y1="12" x2="21.5" y2="12"/><line x1="4" y1="7" x2="20" y2="7"/><line x1="4" y1="17" x2="20" y2="17"/></svg>
        www.kestrelofficeclearance.co.uk
      </li>
    </ul>
  </section>
</body>
</html>
```